Roofing Company Modern look

I want a modern and sophisticated look for our roofing business.

Our address is :

5217 Mallow Creek Ln
Orlando, Fl 32825

(407)-583-2196

www.HarborlineRoofsFl.com

I also want to make sure on the back there is a spot to put
Project Manager Name :

Number:

Because the cards will be used by all sales people

Project Manager Name :

Also there are accreditation we have logos are uploaded here as well that I would like maybe on the back of card as well

I also want to highlight our special attributions or trades:

Residential & Commercial
Fully Insured
License # CCC7482913
Insurance Claims
Serving Central Florida Since 1992
Free Estimates

Contact Information for Business Card

Our address is :

5217 Mallow Creek Ln
Orlando, Fl 32825

(407)-583-2196

Project Manager Name :

Residential & Commercial
Fully Insured
License # CCC7482913
Insurance Claims
Free Estimates

Font styles to use
Serif
Sans Serif

Colors
3176b5

Requirements
Must have
• Must have royal blue like my logo grey and black are the colors I like

```html
<!DOCTYPE html>
<html lang="en">
<head>
<meta charset="utf-8">
<title>Harborline Roofing &amp; Gutters – Business Card</title>
<link href="https://fonts.googleapis.com/css2?family=Roboto+Condensed:wght@300;400;500&family=Michroma&display=swap" rel="stylesheet">
<style>
  :root {
    --royal-blue: #3176b5;
    --blue-deep: #1a65a6;
    --blue-light: #3f9bd8;
    --ink: #1f1f1f;
    --steel: #4a4a4a;
    --grey-mid: #8a8a8a;
    --canvas: #e9e9e9;
    --card: #ffffff;
    --white: #ffffff;
  }
  * { box-sizing: border-box; margin: 0; padding: 0; }
  html, body { width: 1200px; height: 1200px; overflow: hidden; }
  body {
    background: var(--canvas);
    font-family: "Roboto Condensed", Arial, sans-serif;
    position: relative;
  }
  .card {
    position: absolute;
    left: 150px;
    width: 900px;
    height: 514px;
    background: var(--card);
    border-radius: 30px;
    box-shadow: 0 14px 30px rgba(0,0,0,0.22);
    overflow: hidden;
  }
  .card--front { top: 50px; }
  .card--back { top: 636px; }

  .rule {
    position: absolute; left: 0; width: 100%; height: 7px;
    background: linear-gradient(90deg, var(--ink), var(--steel) 50%, var(--ink));
  }
  .band {
    position: absolute; left: 0; width: 100%;
    background: linear-gradient(90deg, var(--blue-deep) 0%, var(--royal-blue) 45%, var(--blue-light) 100%);
    color: var(--white);
  }

  /* Front */
  .brand {
    position: absolute; left: 0; top: 60px; width: 100%;
    text-align: center; color: var(--royal-blue);
    font-weight: 400;
  }
  .brand__mark {
    width: 110px; height: 110px; border-radius: 50%;
    background: var(--royal-blue); margin: 0 auto 26px;
  }
  .brand__name {
    font-size: 58px; letter-spacing: 4px; line-height: 1;
    font-weight: 400;
  }
  .brand__sub {
    margin-top: 10px; font-size: 22px; letter-spacing: 5px; font-weight: 400;
  }
  .card--front .rule--top { top: 357px; }
  .card--front .band { top: 369px; height: 97px; }
  .card--front .rule--bottom { top: 471px; }
  .contact {
    position: absolute; left: 0; width: 100%;
    display: flex; justify-content: center; align-items: center; gap: 8px;
    font-size: 24px; font-weight: 400; letter-spacing: 0.3px;
  }
  .contact--address { top: 14px; }
  .contact--lines { top: 48px; }
  .contact__divider {
    position: absolute; top: 46px; left: 155px; width: 590px; height: 1px;
    background: rgba(255,255,255,0.75);
  }
  .contact svg { width: 22px; height: 22px; flex: none; }
  .contact .gap { width: 6px; }

  /* Back */
  .field {
    position: absolute; left: 68px; right: 70px;
    display: flex; align-items: flex-end; gap: 6px;
    color: var(--royal-blue); font-size: 21px; font-weight: 300;
  }
  .field__line { flex: 1; border-bottom: 1px solid var(--royal-blue); margin-bottom: 5px; }
  .field--manager { top: 50px; }
  .field--phone { top: 121px; }

  .card--back .rule--top { top: 197px; }
  .card--back .band { top: 209px; height: 133px; }
  .card--back .rule--bottom { top: 345px; }
  .traits {
    position: absolute; top: 20px; list-style: none;
    font-size: 24px; font-weight: 400; line-height: 29px;
  }
  .traits--left { left: 64px; }
  .traits--right { left: 424px; }
  .traits li { display: flex; align-items: center; gap: 12px; }
  .traits svg { width: 24px; height: 24px; flex: none; }

  .badges {
    position: absolute; top: 392px; left: 0; width: 100%; height: 75px;
  }
  .badge { position: absolute; top: 50%; transform: translate(-50%, -50%); }
  .badge--shield { left: 100px; width: 60px; height: 75px; border: 2px solid var(--royal-blue); border-radius: 6px; background: #eef4fa; }
  .badge--hex { left: 291px; width: 82px; height: 72px; background: var(--steel); clip-path: polygon(50% 0, 100% 22%, 100% 78%, 50% 100%, 0 78%, 0 22%); }
  .badge--rect { left: 542px; width: 176px; height: 50px; border: 2px solid var(--ink); background: #fbeaea; }
  .badge--seal { left: 792px; width: 72px; height: 72px; border-radius: 50%; border: 5px solid var(--grey-mid); background: #f4f4f4; }
</style>
</head>
<body>

<section class="card card--front" aria-label="Business card front">
  <div class="brand">
    <div class="brand__mark"></div>
    <div class="brand__name">HARBORLINE</div>
    <div class="brand__sub">ROOFING &amp; GUTTERS INC.</div>
  </div>
  <div class="rule rule--top"></div>
  <div class="band">
    <div class="contact contact--address">
      <svg viewBox="0 0 24 24" aria-hidden="true"><circle cx="12" cy="12" r="11" fill="#fff"/><path d="M12 5a4.5 4.5 0 0 0-4.5 4.5c0 3.4 4.5 8.5 4.5 8.5s4.5-5.1 4.5-8.5A4.5 4.5 0 0 0 12 5zm0 6.3a1.8 1.8 0 1 1 0-3.6 1.8 1.8 0 0 1 0 3.6z" fill="#3176b5"/></svg>
      <span>5217 MALLOW CREEK LN, ORLANDO, FL 32825</span>
    </div>
    <div class="contact__divider"></div>
    <div class="contact contact--lines">
      <svg viewBox="0 0 24 24" aria-hidden="true"><circle cx="12" cy="12" r="11" fill="#fff"/><path d="M8.6 6.2l1.9 2.6-1.1 1.4c.8 1.7 2.1 3 3.8 3.8l1.4-1.1 2.6 1.9-.9 2.2c-4.9-.3-8.5-3.9-8.8-8.8z" fill="#3176b5"/></svg>
      <span>(407)-583-2196</span>
      <span class="gap"></span>
      <svg viewBox="0 0 24 24" aria-hidden="true"><circle cx="12" cy="12" r="11" fill="#fff"/><g fill="none" stroke="#3176b5" stroke-width="1.2"><circle cx="12" cy="12" r="6"/><ellipse cx="12" cy="12" rx="2.6" ry="6"/><path d="M6 12h12M7 9h10M7 15h10"/></g></svg>
      <span>WWW.HARBORLINEROOFSFL.COM</span>
    </div>
  </div>
  <div class="rule rule--bottom"></div>
</section>

<section class="card card--back" aria-label="Business card back">
  <div class="field field--manager"><span>PROJECT MANAGER NAME :</span><span class="field__line"></span></div>
  <div class="field field--phone"><span>PHONE:</span><span class="field__line"></span></div>

  <div class="rule rule--top"></div>
  <div class="band">
    <ul class="traits traits--left">
      <li><svg viewBox="0 0 24 24" aria-hidden="true"><path d="M4 12.5l5 5L20 6" fill="none" stroke="#fff" stroke-width="3"/></svg>RESIDENTIAL &amp; COMMERCIAL</li>
      <li><svg viewBox="0 0 24 24" aria-hidden="true"><path d="M4 12.5l5 5L20 6" fill="none" stroke="#fff" stroke-width="3"/></svg>FULLY INSURED</li>
      <li><svg viewBox="0 0 24 24" aria-hidden="true"><path d="M4 12.5l5 5L20 6" fill="none" stroke="#fff" stroke-width="3"/></svg>LICENSE # CCC7482913</li>
    </ul>
    <ul class="traits traits--right">
      <li><svg viewBox="0 0 24 24" aria-hidden="true"><path d="M4 12.5l5 5L20 6" fill="none" stroke="#fff" stroke-width="3"/></svg>INSURANCE CLAIMS</li>
      <li><svg viewBox="0 0 24 24" aria-hidden="true"><path d="M4 12.5l5 5L20 6" fill="none" stroke="#fff" stroke-width="3"/></svg>SERVING CENTRAL FLORIDA SINCE 1992</li>
      <li><svg viewBox="0 0 24 24" aria-hidden="true"><path d="M4 12.5l5 5L20 6" fill="none" stroke="#fff" stroke-width="3"/></svg>FREE ESTIMATES</li>
    </ul>
  </div>
  <div class="rule rule--bottom"></div>

  <div class="badges">
    <div class="badge badge--shield" role="img" aria-label="Business accreditation badge"></div>
    <div class="badge badge--hex" role="img" aria-label="Shingle applicator certification badge"></div>
    <div class="badge badge--rect" role="img" aria-label="Authorized roofing contractor badge"></div>
    <div class="badge badge--seal" role="img" aria-label="Screened and approved listing seal"></div>
  </div>
</section>

</body>
</html>
```